Business Card Design

Mountain mowing & yard clean up Handy services honey do lists

Card Details:
Jon Keltner
4058813647

Jon Keltner

405 881 3647 
Colo. City, Co.

Industry/Entity Type

Business

Requirements
Must have
• I want a mountain scene with a riding lawn mower

```html
<!DOCTYPE html>
<html lang="en">
<head>
<meta charset="utf-8">
<title>Summit Mowing – Business Card</title>
<link rel="stylesheet" href="https://fonts.googleapis.com/css2?family=Archivo:wght@700&display=swap">
<style>
  :root {
    --brown: #7a4200;
    --forest: #0b5534;
    --leaf-light: #c9df90;
    --leaf-mid: #7aa638;
    --leaf-top: #b4d88d;
    --orange: #f28a2a;
    --paper: #ffffff;
  }
  * { margin: 0; padding: 0; box-sizing: border-box; }
  html, body {
    width: 1200px; height: 703px; overflow: hidden;
    background: var(--paper);
    font-family: "Archivo", Arial, sans-serif;
    font-weight: 700;
  }
  .card { position: relative; width: 1200px; height: 703px; overflow: hidden; background: var(--paper); }
  .stripe { position: absolute; left: 0; width: 100%; }
  .stripe--light { top: 0; height: 20px; background: var(--leaf-top); }
  .stripe--green { top: 25px; height: 13px; background: var(--leaf-mid); }
  .stripe--orange { top: 42px; height: 13px; background: var(--orange); }

  .forest-band { position: absolute; left: 0; bottom: 0; width: 1200px; height: 260px; }

  .mower-art {
    position: absolute; left: 645px; top: 135px; width: 500px; height: 385px;
    border-radius: 40px;
    background: radial-gradient(ellipse at 50% 50%, var(--leaf-light) 60%, #d9e8b4 100%);
  }

  .brand { position: absolute; left: 60px; top: 105px; color: var(--brown); text-transform: uppercase; }
  .brand__main { font-size: 118px; line-height: 1; letter-spacing: 1px; }
  .brand__sub { font-size: 72px; line-height: 1; margin: 10px 0 0 135px; }
  .brand__tag { font-size: 31px; line-height: 1; margin: 24px 0 0 88px; letter-spacing: 3px; }

  .contact { position: absolute; left: 55px; top: 448px; text-transform: uppercase; }
  .contact__name { color: var(--forest); font-size: 60px; line-height: 1; }
  .contact__city { color: var(--brown); font-size: 42px; line-height: 1; margin-top: 22px; }
  .contact__phone { color: var(--brown); font-size: 52px; line-height: 1; margin-top: 16px; }
</style>
</head>
<body>
<main class="card">
  <div class="stripe stripe--light"></div>
  <div class="stripe stripe--green"></div>
  <div class="stripe stripe--orange"></div>

  <svg class="forest-band" viewBox="0 0 1200 260" role="img" aria-label="Silhouette of a pine forest along the bottom of the card">
    <defs>
      <linearGradient id="forestFade" x1="0" y1="0" x2="0" y2="1">
        <stop offset="0" stop-color="#c9df90" stop-opacity="0.55"/>
        <stop offset="1" stop-color="#c9df90"/>
      </linearGradient>
    </defs>
    <rect x="0" y="0" width="1200" height="260" fill="url(#forestFade)"/>
  </svg>

  <div class="mower-art" role="img" aria-label="Illustration of a riding lawn mower"></div>

  <div class="brand">
    <div class="brand__main">Summit</div>
    <div class="brand__sub">Mowing</div>
    <div class="brand__tag">&amp; Yard Clean-Up</div>
  </div>

  <div class="contact">
    <div class="contact__name">Jon Keltner</div>
    <div class="contact__city">Cedar Ridge, Colorado</div>
    <div class="contact__phone"><a href="tel:4058813647" style="color:inherit;text-decoration:none">405 881 3647</a></div>
  </div>
</main>
</body>
</html>
```